Online interactive tutorial for year 2 to year 12 students in Australia

Website design for a new online tutorial for year 2 to year 12 students in Australia.

- The tutorial will be conducted via live webcam and within a dedicated interactive space
- The tutorial will be provided by high scoring undergraduates studying in top Australian universities.
- The tutors will be going through interviews & assessments & only top students are allowed to apply.
- Parents will do search and select tutor and have short 15 mins video interaction with potential tutors before booking them for their children for tutoring.
- hourly cost of booking (no monthly subscription or no hour limits)
- Tutors will have their own profile

Please see the attached for detailed page functionality.

The look and feel of the design must consider the following:
- must be educational but not dull and should stand out
- must appeal to younger generation - tutees (8-18 years), tutors (19-25), parents (30-50).
- Ideas for Logos (brivora.com.au but not confirmed)

Target Market(s)

tutees (8-18 years), tutors (19-25 years), parents (30-50 years).

Industry/Entity Type

Education

Coding

Coded - Design and coding required

Number of Pages Required

5+ page

Font styles to use
Serif

Requirements
Must have
• The look and feel of the design must consider the following:
• - must be educational but not dull and should stand out
• - must appeal to younger generation - tutees (8-18 years), tutors (19-25), parents (30-50).
Should not have
• Dullness

```html
<!DOCTYPE html>
<html lang="en">
<head>
<meta charset="utf-8">
<title>Brivora – Parent's Registration</title>
<link rel="stylesheet" href="https://fonts.googleapis.com/css2?family=Open+Sans:wght@400;600;700&family=Roboto:wght@400;500&family=Roboto+Condensed:wght@700&display=swap">
<style>
:root{
  --blue:#2a7cc1;
  --blue-dark:#1f6aab;
  --cyan:#00a0d6;
  --hero-line:#1ea7e4;
  --ink:#444;
  --muted:#555;
  --field-bg:#f7f7f7;
  --field-line:#e2e2e2;
  --panel:#ebebeb;
  --footer:#333333;
  --white:#ffffff;
}
*{box-sizing:border-box;margin:0;padding:0}
html,body{width:1200px;height:1200px;overflow:hidden}
body{position:relative;background:var(--white);font-family:'Open Sans',sans-serif;color:var(--ink)}
.abs{position:absolute}

/* header */
.brand{left:99px;top:28px;font:700 40px/1 'Open Sans',sans-serif;color:#4a4a4a;display:flex;align-items:center;gap:10px}
.brand .dot{width:38px;height:38px;border-radius:50%;background:var(--blue)}
.search{left:363px;top:37px;width:360px;height:34px;border:1px solid #d6d6d6;border-radius:3px;display:flex;font-size:11px;color:#555}
.search .field{flex:1;padding:0 14px;display:flex;align-items:center;justify-content:space-between}
.search .go{width:38px;background:#e8e8e8;border-left:1px solid #d6d6d6;display:flex;align-items:center;justify-content:center}
.role{top:39px;height:32px;border:2px solid var(--blue);color:var(--blue);font-size:13px;display:flex;align-items:center;justify-content:center;gap:6px}
.login{left:1032px;top:38px;width:69px;height:34px;background:var(--blue);color:#fff;font:400 14px 'Roboto',sans-serif;display:flex;align-items:center;justify-content:center;border-radius:2px;border:1px solid #5aa0da}

/* nav */
.nav{left:0;top:116px;width:1200px;height:49px;background:var(--blue)}
.nav a{position:absolute;top:0;height:49px;line-height:49px;color:#fff;font:400 13.5px/49px 'Roboto',sans-serif;text-decoration:none;transform:translateX(-50%);white-space:nowrap}
.nav i{position:absolute;top:0;width:1px;height:49px;background:#2370b1}

/* hero */
.hero{left:0;top:165px;width:1200px;height:330px}
.hero-title{left:0;top:315px;width:1200px;text-align:center;font:700 45px/1 'Roboto Condensed',sans-serif;color:#fff;letter-spacing:.5px}

/* form */
.input{height:38px;background:var(--field-bg);border:1px solid var(--field-line);font-size:11px;color:var(--muted);padding:0 15px;display:flex;align-items:center;justify-content:space-between}
.input .hint{color:#999;margin-left:6px}
.tab{left:219px;top:651px;width:368px;height:38px;background:linear-gradient(#f6f6f6,#ececec);border:1px solid var(--field-line);font-size:11px;color:var(--muted);text-align:center;line-height:38px}
.child-panel{left:219px;top:689px;width:534px;height:294px;background:var(--panel);border:1px solid #d9d9d9;z-index:5}
.child-panel .input{background:#fafafa;position:absolute;width:235px}
.notch{left:256px;top:674px;z-index:6}
.add-btn{left:214px;top:231px;width:98px;height:31px;background:var(--blue);color:#fff;border-radius:2px;font:500 15px/31px 'Roboto',sans-serif;text-align:center}

/* footer */
.footer{left:0;top:858px;width:1200px;height:291px;background:var(--footer);color:#fff}
.footer h3{position:absolute;top:37px;font:400 18px 'Roboto',sans-serif;letter-spacing:.2px}
.footer p{position:absolute;font-size:12.5px;line-height:20px}
.links{position:absolute;left:428px;list-style:none;font-size:13px}
.links li{height:21.5px;display:flex;align-items:center;gap:9px}
.links li::before{content:"";border-left:4px solid #fff;border-top:4px solid transparent;border-bottom:4px solid transparent}
.news-input{left:624px;top:124px;width:292px;height:41px;background:#fff;color:#555;font-size:11px;padding-left:14px;line-height:41px}
.subscribe{left:623px;top:175px;width:102px;height:41px;background:var(--cyan);color:#fff;font:400 14px/41px 'Roboto',sans-serif;text-align:center}
.social{position:absolute;left:1005px;display:flex;align-items:center;gap:9px;font-size:14.5px}
.social .ring{width:27px;height:27px;border:1.5px solid #cfcfcf;border-radius:50%}
.copyright{left:0;top:1149px;width:1200px;height:51px;background:var(--cyan);color:#fff;font-size:12.5px;text-align:center;line-height:51px}
</style>
</head>
<body>

<header>
  <div class="abs brand"><span class="dot"></span>Brivora</div>
  <div class="abs search">
    <div class="field">Search
      <svg width="8" height="5" viewBox="0 0 8 5"><path d="M0 0h8L4 5z" fill="#555"/></svg>
    </div>
    <div class="go"><svg width="12" height="12" viewBox="0 0 12 12"><circle cx="5" cy="5" r="3.6" fill="none" stroke="#333" stroke-width="1.6"/><path d="M7.6 7.6L11 11" stroke="#333" stroke-width="1.8"/></svg></div>
  </div>
  <div class="abs role" style="left:745px;width:77px">
    <svg width="12" height="13" viewBox="0 0 12 13"><circle cx="6" cy="3.5" r="3" fill="#2a7cc1"/><path d="M0 13c0-4 2.5-6 6-6s6 2 6 6z" fill="#2a7cc1"/></svg>Tutor</div>
  <div class="abs role" style="left:833px;width:82px">
    <svg width="14" height="14" viewBox="0 0 14 14"><circle cx="4" cy="2.5" r="2" fill="#2a7cc1"/><circle cx="10" cy="2.5" r="2" fill="#2a7cc1"/><rect x="1.5" y="5" width="5" height="9" rx="1" fill="#2a7cc1"/><rect x="7.5" y="5" width="5" height="9" rx="1" fill="#2a7cc1"/></svg>Parent</div>
  <div class="abs role" style="left:928px;width:92px">
    <svg width="14" height="13" viewBox="0 0 14 13"><path d="M0 3l7-3 7 3-7 3z" fill="#2a7cc1"/><circle cx="7" cy="6" r="2.5" fill="#2a7cc1"/><path d="M2 13c0-3 2-4.5 5-4.5s5 1.5 5 4.5z" fill="#2a7cc1"/></svg>Tutees</div>
  <div class="login">LOGIN</div>
</header>

<nav class="abs nav">
  <a style="left:141px">HOME</a><i style="left:188px"></i>
  <a style="left:270px">TUTOR PROFILES</a><i style="left:351px"></i>
  <a style="left:421px">HOW IT WORKS</a><i style="left:495px"></i>
  <a style="left:566px">TESTIMONIALS</a><i style="left:640px"></i>
  <a style="left:686px">PRICES</a><i style="left:735px"></i>
  <a style="left:797px">CONTACT US</a>
</nav>

<section>
  <svg class="abs hero" width="1200" height="330" viewBox="0 0 1200 330" role="img" aria-label="Photo of hands typing on a laptop keyboard, darkened">
    <defs>
      <linearGradient id="heroShade" x1="0" y1="0" x2="1" y2="0">
        <stop offset="0" stop-color="#3b3d42"/>
        <stop offset=".45" stop-color="#55575c"/>
        <stop offset=".75" stop-color="#3a3c44"/>
        <stop offset="1" stop-color="#2f3038"/>
      </linearGradient>
    </defs>
    <path d="M0 0H1200V255L600 328L0 255Z" fill="url(#heroShade)"/>
    <path d="M0 255L600 328L1200 255" fill="none" stroke="var(--hero-line)" stroke-width="4"/>
  </svg>
  <h1 class="abs hero-title">PARENT'S REGISTRATION</h1>
</section>

<form>
  <div class="abs input" style="left:219px;top:549px;width:368px">First Name / Last Name</div>
  <div class="abs input" style="left:613px;top:549px;width:368px">Address</div>
  <div class="abs input" style="left:219px;top:600px;width:368px">Email</div>
  <div class="abs input" style="left:613px;top:600px;width:368px">Phone number</div>
  <div class="abs tab">ADD CHILD</div>
  <div class="abs input" style="left:613px;top:651px;width:368px;justify-content:flex-start">Username<span class="hint">(the email address)</span></div>
  <div class="abs input" style="left:613px;top:703px;width:368px"></div>

  <svg class="abs notch" width="40" height="16" viewBox="0 0 40 16"><path d="M0 16L20 1L40 16" fill="var(--panel)" stroke="#d9d9d9"/><rect x="0" y="15" width="40" height="2" fill="var(--panel)"/></svg>
  <div class="abs child-panel">
    <div class="input" style="left:23px;top:26px">First Name / Last Name</div>
    <div class="input" style="left:276px;top:26px;padding-left:12px">School</div>
    <div class="input" style="left:23px;top:77px">Gender<svg width="7" height="4" viewBox="0 0 7 4"><path d="M0 0h7L3.5 4z" fill="#444"/></svg></div>
    <div class="input" style="left:276px;top:77px;padding-left:12px">Tutoring Needs<svg width="7" height="4" viewBox="0 0 7 4"><path d="M0 0h7L3.5 4z" fill="#444"/></svg></div>
    <div class="input" style="left:23px;top:129px">Date of birth<svg width="11" height="11" viewBox="0 0 11 11"><rect x=".5" y="1.5" width="10" height="9" fill="none" stroke="#555"/><path d="M.5 4h10M3 0v3M8 0v3M3 6h1M5 6h1M7 6h1M3 8h1M5 8h1M7 8h1" stroke="#555"/></svg></div>
    <div class="input" style="left:276px;top:129px;padding-left:12px">Username<svg width="7" height="4" viewBox="0 0 7 4"><path d="M0 0h7L3.5 4z" fill="#444"/></svg></div>
    <div class="input" style="left:23px;top:180px">Year of study</div>
    <div class="input" style="left:276px;top:180px;padding-left:12px">Create a password</div>
    <div class="abs add-btn">Add Child</div>
  </div>
</form>

<footer class="abs footer">
  <h3 style="left:98px">CONTACT US</h3>
  <p style="left:99px;top:74px">Level 3, 22 Harbour Lane,<br>QLD 4010, Australia</p>
  <svg class="abs" style="left:101px;top:130px" width="18" height="18" viewBox="0 0 18 18"><path d="M4 1l3 4-2 2c1 2.5 3.5 5 6 6l2-2 4 3-2 3C8 16 2 10 1 4z" fill="none" stroke="#ddd" stroke-width="1.1"/></svg>
  <p style="left:135px;top:126px;font-size:13.5px;line-height:21px">Phone : +61 7 5550 1428<br>Fax : +61 7 5550 1429</p>
  <svg class="abs" style="left:100px;top:184px" width="19" height="13" viewBox="0 0 19 13"><rect x=".5" y=".5" width="18" height="12" fill="none" stroke="#ddd"/><path d="M.5 .5l9 7 9-7M.5 12.5l6.5-6M18.5 12.5l-6.5-6" fill="none" stroke="#ddd"/></svg>
  <p style="left:136px;top:180px;font-size:13.5px">Email: info@brivora.com.au</p>

  <h3 style="left:426px">QUICK LINKS</h3>
  <ul class="links" style="top:70px">
    <li>Home</li><li>About Us</li><li>Prices</li>
  </ul>
  <ul class="links" style="top:124px">
    <li>Services</li><li>Tutor Profile</li><li>How It Works</li><li>Scheduler</li><li>Testimonials</li><li>Contact Us</li>
  </ul>

  <h3 style="left:624px">NEWSLETTER</h3>
  <p style="left:624px;top:72px;font-size:11.5px;line-height:19px">Sed ut perspiciatis unde omnis iste natus error sit volup-<br>tatem accusantium doloremque laudantium,</p>
  <div class="abs news-input">Enter Name</div>
  <div class="abs subscribe">SUBSCRIBE</div>

  <h3 style="left:1006px">SOCIAL</h3>
  <div class="social" style="top:80px"><span class="ring"></span>Friendfeed</div>
  <div class="social" style="top:116px"><span class="ring"></span>Chirper</div>
  <div class="social" style="top:152px"><span class="ring"></span>Circles</div>
  <div class="social" style="top:188px"><span class="ring"></span>Vidstream</div>
</footer>

<div class="abs copyright">Copyright 2016 | All Rights Reserved -- Brivora</div>

</body>
</html>
```